Business Card Design for Occupational Medicine Start Up Company

We need to design a professional business card. We are a healthcare company providing occupational medicine services to blue collar industries. We are professional, efficient and high quality service providers.

Target Market(s)

Blue Collar Industry: Shipbuilding, Ports, Trucking Companies; The Executives and Safety Officers for these companies

Industry/Entity Type

Healthcare

Contact Information for Business Card

Logo, Name, Title, Email, Phone

Other font styles liked:
• Please match our Brand Guide

Requirements
Must have
• Our Company Colors and Logo

```html
<!DOCTYPE html>
<html lang="en">
<head>
<meta charset="utf-8">
<title>Shiftwell Clinics – Business Card</title>
<link rel="stylesheet" href="https://fonts.googleapis.com/css2?family=Montserrat:wght@400;500;700;800&display=swap">
<style>
  :root {
    --bg: #d6d6d6;
    --paper: #f1f1ef;
    --navy: #1f2a7a;
    --sky: #29a3dc;
    --amber: #f4a934;
    --grey: #6d6d6d;
  }
  * { margin: 0; padding: 0; box-sizing: border-box; }
  html, body { width: 1200px; height: 1051px; overflow: hidden; background: var(--bg); }
  body {
    font-family: "Montserrat", Arial, sans-serif;
    display: flex; align-items: center; justify-content: center; gap: 60px;
  }
  .card {
    width: 525px; height: 300px;
    background: var(--paper);
    position: relative;
    box-shadow: 0 14px 30px rgba(0,0,0,0.18);
  }
  .brand {
    color: var(--navy);
    font-weight: 800;
    text-transform: uppercase;
    line-height: 1;
    display: flex; align-items: center; gap: 12px;
  }
  .brand-dot {
    width: 14px; height: 14px; border-radius: 50%;
    background: var(--navy);
  }
  .brand-name { display: flex; flex-direction: column; }
  .brand-name .line-main { font-size: 26px; letter-spacing: 0.5px; }
  .brand-name .line-sub { font-size: 13px; letter-spacing: 8px; margin-top: 6px; }

  /* front */
  .card-front .brand { position: absolute; top: 62px; left: 170px; }
  .holder {
    position: absolute; top: 178px; left: 40px; width: 170px; text-align: right;
  }
  .holder-name { color: var(--navy); font-weight: 800; font-size: 17px; text-transform: uppercase; letter-spacing: 0.3px; }
  .holder-title { color: var(--grey); font-size: 13px; margin-top: 6px; }
  .divider {
    position: absolute; top: 176px; left: 228px; width: 2px; height: 62px; background: var(--amber);
  }
  .contact { position: absolute; top: 174px; left: 248px; list-style: none; }
  .contact li {
    display: flex; align-items: center; gap: 9px;
    color: var(--grey); font-size: 13px; height: 22px;
  }
  .contact svg { width: 12px; height: 12px; fill: var(--sky); flex: none; }

  /* back */
  .card-back { display: flex; align-items: center; justify-content: center; }
  .card-back .brand-name .line-main { font-size: 32px; }
  .card-back .brand-name .line-sub { font-size: 15px; letter-spacing: 10px; }
  .card-back .brand-dot { width: 16px; height: 16px; }
</style>
</head>
<body>
  <section class="card card-front">
    <div class="brand">
      <span class="brand-dot"></span>
      <span class="brand-name"><span class="line-main">Shiftwell</span><span class="line-sub">Clinics</span></span>
    </div>
    <div class="holder">
      <p class="holder-name">Mark Ellison</p>
      <p class="holder-title">President</p>
    </div>
    <div class="divider"></div>
    <ul class="contact">
      <li><svg viewBox="0 0 24 24" aria-hidden="true"><path d="M6.6 10.8a15.1 15.1 0 0 0 6.6 6.6l2.2-2.2a1 1 0 0 1 1-.25 11.4 11.4 0 0 0 3.6.57 1 1 0 0 1 1 1V20a1 1 0 0 1-1 1A17 17 0 0 1 3 4a1 1 0 0 1 1-1h3.5a1 1 0 0 1 1 1c0 1.25.2 2.45.57 3.57a1 1 0 0 1-.25 1z"/></svg>555-014-2871</li>
      <li><svg viewBox="0 0 24 24" aria-hidden="true"><path d="M2 5h20v14H2z M2 5l10 8 10-8" stroke="#f1f1ef" stroke-width="1.5"/></svg>mark@shiftwellclinics.com</li>
      <li><svg viewBox="0 0 24 24" aria-hidden="true"><circle cx="12" cy="12" r="10"/></svg>www.shiftwellclinics.com</li>
    </ul>
  </section>
  <section class="card card-back">
    <div class="brand">
      <span class="brand-dot"></span>
      <span class="brand-name"><span class="line-main">Shiftwell</span><span class="line-sub">Clinics</span></span>
    </div>
  </section>
</body>
</html>
```